Product Label with Company Logo & Product Information

I am looking for a new label design for one of my products, Candied Pecans. I am including an old label that I made, but it does not "pop" on the current packaging. See image of current packaging attached as well.

I want the design to ultimately be something that I can take and order a roll of labels/stickers. Please stick within standard label/sticker sizes (round or square). Please include final size as well.

Must Haves:
(1) Company logo (any color variation-see attached logo images).
(2) All wording on the old label
(3) Label size can not be more than 2 in. x 4 in. (I would actually like them a little smaller). They seem kind of big as they are right now.

```html
<!DOCTYPE html>
<html lang="en">
<head>
<meta charset="utf-8">
<title>Gourmet Candied Pecans Label</title>
<link rel="stylesheet" href="https://fonts.googleapis.com/css2?family=Abril+Fatface&family=Rye&family=Pirata+One&family=Montserrat:wght@700&display=swap">
<style>
  :root {
    --backdrop: #232323;
    --label-black: #1f1f22;
    --label-grey: #58585a;
    --label-grey-light: #6e6e70;
    --honey: #f2ea22;
    --edge-dark: #141416;
  }
  * { margin: 0; padding: 0; box-sizing: border-box; }
  html, body {
    width: 1200px; height: 780px; overflow: hidden;
    background: var(--backdrop);
  }
  .label {
    position: absolute; left: 100px; top: 110px;
    width: 1000px; height: 560px;
    background: var(--label-black);
    border: 5px solid var(--honey);
    overflow: hidden;
  }
  .label__swoosh { position: absolute; inset: 0; width: 100%; height: 100%; }
  .title { position: absolute; left: 60px; top: 48px; font-weight: 400; }
  .title__main {
    font-family: "Abril Fatface", serif;
    font-size: 78px; line-height: 1; color: var(--honey);
    letter-spacing: 1px;
  }
  .title__sub {
    display: inline-block;
    font-family: "Rye", serif;
    font-size: 54px; line-height: 1.1; color: var(--label-grey);
    -webkit-text-stroke: 2px var(--honey);
    margin-top: 6px; margin-left: 30px; letter-spacing: 1px;
  }
  .brand {
    position: absolute; right: 70px; top: 60px;
    display: flex; align-items: center; gap: 16px;
  }
  .brand__dot { width: 46px; height: 46px; border-radius: 50%; background: var(--honey); }
  .brand__name {
    font-family: "Pirata One", cursive;
    font-size: 72px; line-height: 1; color: var(--honey);
  }
  .details {
    position: absolute; left: 90px; bottom: 40px;
    font-family: "Pirata One", cursive;
    color: var(--honey); font-size: 34px; line-height: 1.15;
  }
  .details__phone {
    display: flex; align-items: center; gap: 14px;
    font-family: "Montserrat", sans-serif; font-weight: 700;
    font-size: 36px; margin: 8px 0 4px;
  }
  .details__icon { width: 46px; height: 46px; }
</style>
</head>
<body>
  <main class="label">
    <svg class="label__swoosh" viewBox="0 0 1000 560" preserveAspectRatio="none" aria-hidden="true">
      <path d="M0 250 C 300 190, 700 290, 1000 330 L1000 560 L0 560 Z" fill="var(--label-grey)"/>
      <path d="M0 272 C 300 222, 700 322, 1000 382 L1000 398 C 700 338, 300 242, 0 288 Z" fill="var(--edge-dark)"/>
      <path d="M40 262 C 320 205, 700 305, 1000 348 L1000 388 C 700 332, 320 226, 40 262 Z" fill="var(--honey)"/>
    </svg>

    <div class="brand">
      <span class="brand__dot"></span>
      <span class="brand__name">Clover Hive</span>
    </div>

    <h1 class="title">
      <span class="title__main">GOURMET</span><br>
      <span class="title__sub">CANDIED PECANS</span>
    </h1>

    <section class="details">
      <p class="details__line">Made with Cinnamon</p>
      <p class="details__line">Brown Sugar &amp; Salt Order More</p>
      <p class="details__phone">
        <svg class="details__icon" viewBox="0 0 46 46" aria-hidden="true">
          <polygon points="23,2 42,12 42,34 23,44 4,34 4,12" fill="var(--honey)"/>
          <path d="M15 14 l5 -1 3 6 -3 2 c1 3 4 6 7 7 l2 -3 6 3 -1 5 c-10 1 -20 -9 -19 -19z" fill="var(--label-grey)"/>
        </svg>
        (555)014-2739
      </p>
      <p class="details__line">Clover Hive Market, LLC</p>
    </section>
  </main>
</body>
</html>
```